Geschäftspapiere für Jobwebseite
Zielgruppe
Hier finden sie alle Informationen zu unserem Unternehmen:
https://www.sauberwerk-stelle.com
Aufgabenstellung
Gerne von den Farben angelehnt an die Website ein modernes Briefpapier gestalten.

```html
<!DOCTYPE html>
<html lang="de">
<head>
<meta charset="utf-8">
<title>Briefpapier – sauberwerk-stelle.de</title>
<link rel="stylesheet" href="https://fonts.googleapis.com/css2?family=Lato:wght@400;700;900&display=swap">
<style>
  :root {
    --brand-green: #16913a;
    --ink: #2f3033;
    --text: #1e1e1e;
    --paper: #ffffff;
    --faint-grey: #c4c3c5;
    --faint-green: #dbe8d6;
  }
  * { margin: 0; padding: 0; box-sizing: border-box; }
  html, body { width: 857px; height: 1200px; overflow: hidden; background: var(--paper); }
  body { font-family: "Lato", sans-serif; color: var(--text); }

  .letterhead { position: relative; width: 857px; height: 1200px; background: var(--paper); }

  .side-band { position: absolute; left: 0; top: 0; width: 80px; height: 100%; background: var(--brand-green); }

  .brand-name {
    position: absolute; right: 52px; top: 104px;
    font-weight: 900; font-size: 31px; letter-spacing: 0.2px;
    color: var(--ink); white-space: nowrap;
  }
  .brand-dot {
    position: absolute; left: 674px; top: 142px;
    width: 24px; height: 24px; border-radius: 50%;
    background: var(--brand-green);
  }

  .sender-line {
    position: absolute; left: 122px; top: 246px; width: 326px;
    font-size: 9.5px; letter-spacing: 0.2px; white-space: nowrap;
    padding-bottom: 4px; border-bottom: 2px solid var(--brand-green);
  }

  .decor { position: absolute; border-radius: 50% 50% 45% 45%; }
  .decor--grey {
    left: 170px; top: 470px; width: 100px; height: 200px;
    background: radial-gradient(ellipse at center, var(--faint-grey) 0%, rgba(196,195,197,0) 70%);
  }
  .decor--green {
    left: 495px; top: 642px; width: 115px; height: 260px;
    background: radial-gradient(ellipse at center, var(--faint-green) 0%, rgba(219,232,214,0) 70%);
  }

  .footer-rule {
    position: absolute; left: 177px; top: 1069px; width: 621px;
    border-top: 2px solid var(--brand-green);
  }
  .footer-mark {
    position: absolute; left: 104px; top: 1096px;
    width: 48px; height: 48px; border-radius: 50%;
    background: var(--brand-green);
  }
  .footer-col {
    position: absolute; top: 1085px;
    font-size: 15px; line-height: 23px; letter-spacing: 1.1px; white-space: nowrap;
  }
  .footer-col--address { left: 204px; }
  .footer-col--bank { right: 109px; text-align: right; }
</style>
</head>
<body>
  <div class="letterhead">
    <div class="side-band"></div>

    <div class="brand-name">SAUBERWERK-STELLE.de</div>
    <div class="brand-dot"></div>

    <p class="sender-line">sauberwerk-stelle.de | Gewerbering Nord 12 | 12345 Musterstadt</p>

    <div class="decor decor--grey" role="img" aria-label="Dezente graue Dekorationsfläche"></div>
    <div class="decor decor--green" role="img" aria-label="Dezente hellgrüne Dekorationsfläche"></div>

    <div class="footer-rule"></div>
    <div class="footer-mark"></div>
    <div class="footer-col footer-col--address">
      Gewerbering Nord 12<br>
      12345 Musterstadt<br>
      E-Mail: info@sauberwerk-stelle.de<br>
      URL: www.sauberwerk-stelle.de
    </div>
    <div class="footer-col footer-col--bank">
      Tel.: 01234 567 890 1<br>
      Ust.-ID: 1234568<br>
      Beispielbank<br>
      IBAN: DE123456789
    </div>
  </div>
</body>
</html>
```